Need a stunning home page for Car rental company

For a client, I need a slick and sumber home page design. It is a small, local car rental company, with a handful of cars available for rent.
Selling points: affordable lease, availability, always clean cars
The design should be:
- flat and modern
- no, or very few animations/sliders
- CTA: booking form for renting a car.
- 3 featured cars with images and facts (see website) with button to read more about the car.
- fullscreen background video can be an option
- main colour: #efba01
The site is under construction here:
http://solvikutleie.hammerlia.no/
Delivery requirements:
I need a layered & well organised PSD file delivered.

```html
<!DOCTYPE html>
<html lang="no">
<head>
<meta charset="utf-8">
<title>Solvik Utleie – Bilutleie i Hammerlia</title>
<link href="https://fonts.googleapis.com/css2?family=Open+Sans:wght@400;600;700&family=Oswald:wght@400;500&display=swap" rel="stylesheet">
<style>
:root{
  --brand:#efba01;
  --brand-dark:#c99a00;
  --ink:#333333;
  --muted:#777777;
  --line:#e2e2e2;
  --page:#ffffff;
  --band:#eeeeee;
  --panel:rgba(20,20,20,.78);
  --footer:#e9e9e9;
  --footer-ink:#666666;
  --bar:#3a3a3a;
}
*{box-sizing:border-box;margin:0;padding:0}
html,body{width:1200px;height:2320px;overflow:hidden}
body{font-family:"Open Sans",Arial,sans-serif;color:var(--ink);background:var(--page);font-size:15px}
.site{width:1200px;height:2320px;position:relative}

/* header */
.header{height:140px;position:relative;padding:0 90px}
.logo{position:absolute;left:90px;top:38px;font-family:"Oswald",Arial,sans-serif;font-size:34px;font-weight:500;color:var(--brand);letter-spacing:1px;text-transform:uppercase}
.topbar{position:absolute;right:90px;top:22px;display:flex;gap:26px;font-size:12px;color:var(--muted);align-items:center}
.topbar .lang{border:1px solid var(--line);padding:3px 10px;color:var(--brand)}
.nav{position:absolute;right:90px;top:80px;display:flex;gap:0}
.nav a{display:block;padding:10px 17px;font-size:14px;color:var(--ink);text-decoration:none}
.nav a.active{background:var(--brand);color:#fff}

/* hero */
.hero{position:absolute;top:140px;left:0;width:1200px;height:530px}
.hero-photo{position:absolute;inset:0;background:linear-gradient(110deg,#9aa6b2 0%,#4c5561 35%,#1d2127 60%,#5a2a22 85%,#2a1c1a 100%)}
.hero-arrow{position:absolute;top:240px;width:30px;height:50px}
.booking{position:absolute;right:90px;top:28px;width:410px;height:440px;background:var(--panel);padding:26px 24px;color:#fff}
.booking h2{font-family:"Oswald",Arial,sans-serif;font-weight:400;font-size:30px;text-align:center;letter-spacing:1px}
.booking .sub{text-align:center;font-size:13px;color:#ccc;margin:4px 0 20px}
.field{height:40px;border-bottom:1px solid rgba(255,255,255,.25);display:flex;align-items:center;justify-content:space-between;font-size:14px;color:#eee;margin-bottom:8px;padding:0 4px}
.field .cal{width:18px;height:18px;background:var(--brand)}
.check{display:flex;align-items:center;gap:10px;font-size:13px;margin:12px 4px 16px}
.check span.box{width:14px;height:14px;background:#fff}
.btn{display:inline-block;background:var(--brand);color:#fff;font-size:14px;padding:9px 28px;border:0;text-transform:uppercase}
.booking .btn{display:block;margin:0 auto;width:140px;text-align:center}

/* featured */
.featured{position:absolute;top:670px;left:0;width:1200px;height:680px;background:var(--band);padding:70px 90px}
.cards{display:flex;gap:22px}
.card{width:326px;background:#fff;box-shadow:0 2px 6px rgba(0,0,0,.15);position:relative;height:530px}
.card-photo{height:190px}
.price{position:absolute;left:16px;top:150px;background:var(--brand);color:#fff;font-size:12px;padding:8px 14px;line-height:1.3}
.card h3{font-family:"Oswald",Arial,sans-serif;font-weight:400;color:var(--brand);text-align:center;font-size:22px;margin:40px 0 12px}
.specs{width:270px;margin:0 auto;border-collapse:collapse;font-size:12px}
.specs td{padding:5px 0;border-top:1px solid var(--line)}
.specs td:last-child{text-align:left;width:90px}
.card .btn{display:block;width:120px;margin:22px auto 0;text-align:center;font-size:13px;padding:7px 0;text-transform:none}

/* video */
.video{position:absolute;top:1350px;left:0;width:1200px;height:610px;background:linear-gradient(180deg,#7d8791 0%,#a7b0b8 55%,#6b737b 100%)}
.play{position:absolute;left:560px;top:270px}
.controls{position:absolute;left:90px;top:510px;width:1020px;height:34px;background:rgba(40,40,40,.85);display:flex;align-items:center;padding:0 14px;gap:14px;color:#fff;font-size:12px}
.progress{flex:1;height:6px;background:#666;position:relative}
.progress i{position:absolute;left:0;top:0;height:6px;width:38%;background:var(--brand)}

/* welcome */
.welcome{position:absolute;top:1960px;left:0;width:1200px;padding:58px 260px 0;text-align:center}
.welcome h2{font-family:"Oswald",Arial,sans-serif;font-weight:400;color:var(--brand);font-size:26px;margin-bottom:14px}
.welcome p{font-size:13px;line-height:1.7;color:var(--muted)}

/* footer */
.footer{position:absolute;top:2130px;left:0;width:1200px;height:190px;background:var(--footer);padding:24px 90px 0}
.cols{display:flex;gap:60px}
.col h4{font-size:12px;color:var(--brand);text-transform:uppercase;margin-bottom:10px;font-weight:700}
.col a{display:block;font-size:12px;color:var(--footer-ink);text-decoration:none;line-height:1.8}
.newsletter{margin-left:auto;width:260px}
.newsletter .input{height:30px;background:#fff;display:flex;justify-content:space-between;align-items:center;padding:0 0 0 10px;font-size:12px;color:#999}
.newsletter .input span.go{width:30px;height:30px;background:var(--brand)}
.social{display:flex;gap:18px;margin-top:26px;padding-left:10px}
.social i{width:26px;height:26px;border-radius:50%;background:#555;display:block}
.copy{position:absolute;left:0;bottom:0;width:1200px;height:38px;background:#dcdcdc;font-size:11px;color:var(--footer-ink);padding:12px 90px}
</style>
</head>
<body>
<div class="site">

<header class="header">
  <div class="logo">Solvik Utleie</div>
  <div class="topbar"><span>Spørsmål? Ring oss: 40 12 34 56</span><span>Logg inn</span><span class="lang">NORSK ▾</span></div>
  <nav class="nav">
    <a class="active" href="#">Hjem</a><a href="#">Biler</a><a href="#">Tjenester</a><a href="#">Kontakt oss</a><a href="#">Blog</a><a href="#">Page templates</a><a href="#">About us</a>
  </nav>
</header>

<section class="hero">
  <div class="hero-photo" role="img" aria-label="Grå sedan kjørende på en bygate om kvelden"></div>
  <svg class="hero-arrow" style="left:20px" viewBox="0 0 30 50"><path d="M22 8 8 25l14 17" fill="none" stroke="#fff" stroke-width="4"/></svg>
  <svg class="hero-arrow" style="right:20px" viewBox="0 0 30 50"><path d="M8 8l14 17L8 42" fill="none" stroke="#fff" stroke-width="4"/></svg>
  <form class="booking">
    <h2>BOOKING TO RENT CAR</h2>
    <p class="sub">Sit amet consectetur adipisicing elit</p>
    <div class="field">Type of Car <span>▾</span></div>
    <div class="field">Location</div>
    <div class="field">Pick Up Date <span class="cal"></span></div>
    <div class="field">Drop Off Date <span class="cal"></span></div>
    <div class="check"><span class="box"></span>Available</div>
    <span class="btn">Search</span>
  </form>
</section>

<section class="featured">
  <div class="cards">
    <article class="card">
      <div class="card-photo" role="img" aria-label="Hvit SUV parkert foran bygninger" style="background:linear-gradient(160deg,#8fb4d6,#d9dee3 60%,#7a7f85)"></div>
      <div class="price">Pris<br>kr 690</div>
      <h3>Varebilen</h3>
      <table class="specs">
        <tr><td>Biltype</td><td>Varebil</td></tr><tr><td>Merke, pers</td><td>3</td></tr><tr><td>Ant. dører</td><td>5</td></tr><tr><td>Min. sjåføralder</td><td>21</td></tr><tr><td>Girtype</td><td>Manuell</td></tr><tr><td>Klimaanlegg</td><td>Ja</td></tr><tr><td>Ubegrenset km?</td><td>Nei</td></tr>
      </table>
      <span class="btn">Detaljer</span>
    </article>
    <article class="card">
      <div class="card-photo" role="img" aria-label="Rød sportsbil under blå himmel" style="background:linear-gradient(160deg,#6f9fcf,#c9d7e4 55%,#b02a22)"></div>
      <div class="price">Pris<br>kr 690</div>
      <h3>Varebilen</h3>
      <table class="specs">
        <tr><td>Biltype</td><td>Varebil</td></tr><tr><td>Merke, pers</td><td>3</td></tr><tr><td>Ant. dører</td><td>5</td></tr><tr><td>Min. sjåføralder</td><td>21</td></tr><tr><td>Girtype</td><td>Manuell</td></tr><tr><td>Klimaanlegg</td><td>Ja</td></tr><tr><td>Ubegrenset km?</td><td>Nei</td></tr>
      </table>
      <span class="btn">Detaljer</span>
    </article>
    <article class="card">
      <div class="card-photo" role="img" aria-label="Blå sedan på vei langs kysten" style="background:linear-gradient(160deg,#9cc3e3,#e4e9ee 55%,#2a4f8a)"></div>
      <div class="price">Pris<br>kr 690</div>
      <h3>Varebilen</h3>
      <table class="specs">
        <tr><td>Biltype</td><td>Varebil</td></tr><tr><td>Merke, pers</td><td>3</td></tr><tr><td>Ant. dører</td><td>5</td></tr><tr><td>Min. sjåføralder</td><td>21</td></tr><tr><td>Girtype</td><td>Manuell</td></tr><tr><td>Klimaanlegg</td><td>Ja</td></tr><tr><td>Ubegrenset km?</td><td>Nei</td></tr>
      </table>
      <span class="btn">Detaljer</span>
    </article>
  </div>
</section>

<section class="video" role="img" aria-label="Video av rød kompaktbil i lyst studio">
  <svg class="play" width="80" height="60" viewBox="0 0 80 60"><rect width="80" height="60" rx="6" fill="rgba(30,30,30,.8)"/><path d="M32 18v24l20-12z" fill="#fff"/></svg>
  <div class="controls">
    <svg width="12" height="14" viewBox="0 0 12 14"><path d="M0 0v14l12-7z" fill="#fff"/></svg>
    <div class="progress"><i></i></div>
    <span>02:36</span><span>HD</span>
    <svg width="16" height="16" viewBox="0 0 16 16"><path d="M1 6V1h5M10 1h5v5M15 10v5h-5M6 15H1v-5" fill="none" stroke="#fff" stroke-width="2"/></svg>
  </div>
</section>

<section class="welcome">
  <h2>Velkommen til Solvik Utleie – Hammerlia</h2>
  <p>Solvik Utleie er en lokal bilutleie i Hammerlia. Vi tilbyr rimelige leiebiler, god tilgjengelighet og alltid rene biler. Ta kontakt med oss for et godt tilbud på bil til hverdag, ferie og helg. Velkommen innom oss i dag.</p>
</section>

<footer class="footer">
  <div class="cols">
    <div class="col"><h4>Company</h4><a>About us</a><a>Services</a><a>Presentation</a></div>
    <div class="col"><h4>Specialists</h4><a>Commercial</a><a>Residential</a><a>Luxury</a></div>
    <div class="col"><h4>Advice</h4><a>FAQs</a><a>Support</a></div>
    <div class="col"><h4>Answers</h4><a>Sign Up</a><a>Forums</a><a>Promotions</a></div>
    <div class="col newsletter"><h4>Newsletter Sign Up</h4><div class="input">Enter your Email to join<span class="go"></span></div>
      <div class="social"><i></i><i></i><i></i><i></i></div></div>
  </div>
  <div class="copy">Copy Right © 2014. All rights reserved.</div>
</footer>

</div>
</body>
</html>
```